Business Card Update, need to bring life to the card, two sided color

We need a new business card design, are moving and changing addresses and need a new look, we have the logos already attached but need a new style moving forward. Can incorporate the color of the logo (The Green) as well, maybe a solid back? We deal with safety products revolving around static electricity and safety lighting. Would like to keep same font in second logo as well.

Target Market(s)

Electrical Safety, Lighting

Contact Information for Business Card

Dale Fenwick
Vice President
Office: 770-555-4821
Cell: 770-555-3067
dale@tkfenwick.example
www.tkfenwick.example
4700 West Harbor Boulevard
Suite #150
Roswell, GA 30076

Font styles to use
Serif
Sans Serif

Requirements
Must have
• Since 1918
Nice to have
• Could use the 100 Year Logo for back of card, would like the back of card to be the same green as logo.
Should not have
• No black cards please.

```html
<!DOCTYPE html>
<html lang="en">
<head>
<meta charset="utf-8">
<title>T.K. Fenwick Business Card</title>
<link rel="stylesheet" href="https://fonts.googleapis.com/css2?family=Arimo:wght@700&family=Open+Sans:wght@400&display=swap">
<style>
  :root {
    --brand-green: #009959;
    --page-bg: #edf3f0;
    --page-border: #1a1a1a;
    --card-white: #ffffff;
    --ink: #1b1b1b;
    --ink-dark: #22302a;
  }
  * { margin: 0; padding: 0; box-sizing: border-box; }
  html, body { width: 1200px; height: 862px; overflow: hidden; }
  body {
    background: var(--page-bg);
    border: 4px solid var(--page-border);
    position: relative;
    font-family: "Open Sans", sans-serif;
  }
  .card {
    position: absolute;
    width: 646px;
    height: 369px;
    border-radius: 28px;
    overflow: hidden;
  }
  .card--front {
    left: 52px; top: 30px;
    background: var(--card-white);
    border: 1px solid #333;
  }
  .card--back {
    left: 501px; top: 446px;
    width: 644px; height: 368px;
    background: var(--brand-green);
  }
  .wave { position: absolute; left: 0; top: 0; width: 100%; height: 100%; }
  .abs { position: absolute; white-space: nowrap; }
  .brand-mark {
    position: absolute;
    border-radius: 50%;
  }
  .card--front .brand-mark {
    left: 65px; top: 19px; width: 90px; height: 90px;
    background: var(--brand-green);
  }
  .brand-name {
    font-family: "Arimo", sans-serif;
    font-weight: 700;
    color: var(--brand-green);
  }
  .card--front .brand-name { left: 170px; top: 42px; font-size: 32px; }
  .card--front .brand-sub { left: 191px; top: 72px; font-size: 17px; letter-spacing: 0.3px; }
  .address { left: 63px; top: 135px; font-size: 16px; line-height: 20px; color: var(--ink); }
  .contact {
    left: 63px; font-size: 16px; color: var(--ink);
    display: flex; align-items: center; gap: 4px;
  }
  .contact svg { width: 14px; height: 14px; }
  .contact--phone { top: 196px; }
  .contact--email { top: 225px; }
  .contact--web { top: 258px; }
  .person {
    left: 398px; width: 200px; text-align: center;
    font-family: "Arimo", sans-serif; font-weight: 700; font-size: 24px;
  }
  .person__name { top: 282px; color: var(--card-white); }
  .person__title { top: 312px; color: var(--ink-dark); }

  .card--back .brand-mark {
    left: 36px; top: 105px; width: 136px; height: 136px;
    background: #111;
  }
  .card--back .brand-name { left: 173px; top: 145px; font-size: 45px; color: #111; }
  .card--back .brand-sub { left: 203px; top: 191px; font-size: 23px; color: #111; letter-spacing: 0.4px; }
  .back-web {
    left: 0; width: 100%; top: 331px; text-align: center;
    font-size: 18px; letter-spacing: 4px; color: #1d2a22;
  }
</style>
</head>
<body>
  <section class="card card--front">
    <svg class="wave" viewBox="0 0 713 407" preserveAspectRatio="none" aria-hidden="true">
      <path d="M0,263 C40,350 110,368 200,366 C360,350 520,262 713,300 L713,407 L0,407 Z" fill="var(--brand-green)"/>
      <path d="M330,330 C470,280 600,240 705,270 C610,262 500,285 360,330 Z" fill="var(--brand-green)"/>
      <path d="M38,357 C120,405 250,380 400,332 C520,294 620,258 705,272 C620,262 520,298 400,342 C250,392 110,410 38,357 Z" fill="var(--card-white)"/>
    </svg>

    <div class="brand-mark"></div>
    <div class="abs brand-name">T.K. Fenwick</div>
    <div class="abs brand-name brand-sub">Manufacturing Company, Inc.</div>

    <p class="abs address">123, Street Name, City Name<br>Zipcode - 012345</p>

    <div class="abs contact contact--phone">
      <svg viewBox="0 0 16 16" aria-hidden="true"><circle cx="8" cy="8" r="7" fill="none" stroke="#1b1b1b" stroke-width="1.4"/><path d="M5.3,4.2 L6.6,4 L7.2,5.8 L6.4,6.6 C6.9,7.8 8,8.9 9.3,9.5 L10.1,8.7 L11.9,9.3 L11.7,10.6 C8,11 5,8 5.3,4.2 Z" fill="#1b1b1b"/></svg>
      <span>770-555-4821</span>
    </div>
    <div class="abs contact contact--email">
      <svg viewBox="0 0 16 16" aria-hidden="true"><circle cx="8" cy="8" r="7" fill="none" stroke="#1b1b1b" stroke-width="1.4"/><rect x="4.2" y="5.5" width="7.6" height="5.2" fill="none" stroke="#1b1b1b" stroke-width="1.1"/><path d="M4.2,5.5 L8,8.4 L11.8,5.5" fill="none" stroke="#1b1b1b" stroke-width="1.1"/></svg>
      <span>dale@tkfenwick.example</span>
    </div>
    <div class="abs contact contact--web">
      <svg viewBox="0 0 16 16" aria-hidden="true"><circle cx="8" cy="8" r="6.5" fill="none" stroke="#1b1b1b" stroke-width="1.3"/><ellipse cx="8" cy="8" rx="2.8" ry="6.5" fill="none" stroke="#1b1b1b" stroke-width="1"/><path d="M1.5,8 H14.5 M2.5,5 H13.5 M2.5,11 H13.5" stroke="#1b1b1b" stroke-width="1"/></svg>
      <span>www.tkfenwick.example</span>
    </div>

    <div class="abs person person__name">Dale Fenwick</div>
    <div class="abs person person__title">President</div>
  </section>

  <section class="card card--back">
    <div class="brand-mark"></div>
    <div class="abs brand-name">T.K. Fenwick</div>
    <div class="abs brand-name brand-sub">Manufacturing Company, Inc.</div>
    <div class="abs back-web">www.tkfenwick.example</div>
  </section>
</body>
</html>
```